Quillfen Climate Business Card Design

Design new, 2 sides, business cards for a residential and light commercial heating, air conditioning contractor.

Target Market(s)

Homeowners, small businesses

Industry/Entity Type

Business

Contact Information for Business Card

Dominic Westerhall
Phone - 862-415-2736
Email
Address - PO box 518
Brightwater NJ 07912
Website - www.HarborBreezeLLC.example

Requirements
Must have
• logo, company colors, standard size with no die cut, so I can use nova stamp

```html
<!DOCTYPE html>
<html lang="en">
<head>
<meta charset="utf-8">
<title>Quillfen Climate Business Card</title>
<link rel="stylesheet" href="https://fonts.googleapis.com/css2?family=Open+Sans:ital,wght@0,400;0,600;0,700;1,400&display=swap">
<style>
  :root {
    --brand-red: #9b1c31;
    --brand-orange: #f7941d;
    --text-grey: #555555;
    --card-white: #ffffff;
    --backdrop: #e4e4e4;
  }
  * { margin: 0; padding: 0; box-sizing: border-box; }
  html, body { width: 1200px; height: 1058px; overflow: hidden; }
  body {
    background: var(--backdrop);
    font-family: "Open Sans", Arial, sans-serif;
    position: relative;
  }
  .card {
    position: absolute;
    left: 280px;
    width: 640px;
    height: 366px;
    background: var(--card-white);
    overflow: hidden;
  }
  .card--front { top: 133px; }
  .card--back { top: 559px; }

  .corner-accent {
    position: absolute;
    width: 76px;
    height: 86px;
    background: var(--brand-red);
    border: 2px solid var(--brand-orange);
  }
  .corner-accent--top-left {
    left: -2px; top: -2px;
    border-radius: 0 0 60px 0;
  }
  .corner-accent--bottom-right {
    right: -2px; bottom: -2px;
    border-radius: 60px 0 0 0;
  }

  .brand-name {
    position: absolute;
    left: 40px;
    top: 128px;
    width: 250px;
    text-align: center;
    font-weight: 700;
    font-size: 34px;
    line-height: 1.1;
    color: var(--brand-red);
  }

  .contact {
    position: absolute;
    left: 331px;
    top: 60px;
  }
  .contact__name {
    font-size: 21px;
    font-weight: 700;
    color: var(--brand-red);
    letter-spacing: 0.3px;
    line-height: 26px;
  }
  .contact__title {
    font-size: 16px;
    font-weight: 700;
    color: var(--brand-orange);
    line-height: 22px;
    margin-bottom: 8px;
  }
  .contact__list { list-style: none; }
  .contact__item {
    display: flex;
    align-items: center;
    font-size: 16px;
    color: var(--text-grey);
    line-height: 24.5px;
    white-space: nowrap;
  }
  .contact__icon {
    width: 16px;
    height: 16px;
    margin-right: 9px;
    fill: var(--brand-red);
    flex: none;
  }
  .contact__address {
    margin-top: 6px;
    margin-left: 3px;
    font-size: 16px;
    color: var(--text-grey);
    line-height: 24.5px;
    font-style: normal;
  }

  .services {
    position: absolute;
    left: 0; right: 0;
    top: 170px;
    text-align: center;
    font-style: italic;
    font-size: 17px;
    line-height: 25px;
    color: #222222;
  }
</style>
</head>
<body>
  <section class="card card--front">
    <div class="corner-accent corner-accent--top-left" role="img" aria-label="Decorative brand-colour corner flourish"></div>
    <div class="corner-accent corner-accent--bottom-right" role="img" aria-label="Decorative brand-colour corner flourish"></div>

    <div class="brand-name">Quillfen Climate</div>

    <div class="contact">
      <div class="contact__name">DOMINIC WESTERHALL</div>
      <div class="contact__title">CEO/Founder</div>
      <ul class="contact__list">
        <li class="contact__item">
          <svg class="contact__icon" viewBox="0 0 16 16" aria-hidden="true"><path d="M3.6 1.2l2.3 2.6-1.2 2c.9 2 2.5 3.6 4.5 4.5l2-1.2 2.6 2.3-1.3 2.3C7.2 13.8 2.2 8.8 1.3 2.5z"/></svg>
          862 415 2736
        </li>
        <li class="contact__item">
          <svg class="contact__icon" viewBox="0 0 16 16" aria-hidden="true"><path d="M4.5 1h7v14h-7zM5.8 2.5v9.5h4.4V2.5z"/><circle cx="8" cy="13.4" r=".8" fill="#fff"/></svg>
          862 415 2790
        </li>
        <li class="contact__item">
          <svg class="contact__icon" viewBox="0 0 16 16" aria-hidden="true"><path d="M4 1h8v4H4zM1 6h14v6h-2v3H3v-3H1zM4.5 10v3.5h7V10z"/></svg>
          862 415 2745
        </li>
        <li class="contact__item">
          <svg class="contact__icon" viewBox="0 0 16 16" aria-hidden="true"><path d="M1 3.5h14v1.2L8 9 1 4.7zM1 6.2l7 4.3 7-4.3V13H1z"/></svg>
          dominic@quillfenclimate.example
        </li>
        <li class="contact__item">
          <svg class="contact__icon" viewBox="0 0 16 16" aria-hidden="true"><circle cx="8" cy="8" r="7"/><path d="M5 4.5c1.5.5 2 1.5 1.5 2.5s-2 1-2 2.5 1 2 1 3M10 3c-.5 1.5 0 2.5 1.5 3s1.5 2 1 3" stroke="#fff" stroke-width="1.2" fill="none"/></svg>
          www.quillfenclimatellc.example
        </li>
      </ul>
      <address class="contact__address">
        PO box 518<br>
        Brightwater NJ 07912
      </address>
    </div>
  </section>

  <section class="card card--back">
    <p class="services">
      Residential &amp; light commercial heating<br>
      Air conditioning contractor
    </p>
  </section>
</body>
</html>
```